Amber Ledger of Kite Keepers

Hi - I would like your help transforming my (terrible) drawing into a graphic that pops -using hex colors I'll give you - so that I can put it into stationary and on t-shirts or tote bags. My company, the Quillmark Institute, trains social change leaders (from the sectors in the periodic table) on how to lead large-scale change. I have this vision - the "periodic table" but these are the sectors that my clients work in. If you are having trouble reading my writing, I apologize. Our hex colors are: #114769, #76984C, #80B5CF (Seagull), #8F2C63 and Rangoon Black #191919. You don't need to use all of them, but it'd be good to be consistent with our overall branding. If you can't read my writing, I will send correct spelling. The "Quillmark" with the flowers on the bottom is for a separate design bid.

Target Market(s)

nonprofit, social entrepreneurs, philanthropy, leaders

Requirements
Must have
• clean, readable font. alignment to look like periodic table of elements. heart icon for love, cat face for cats.

```html
<!DOCTYPE html>
<html lang="en">
<head>
<meta charset="utf-8">
<title>Amber Ledger of Kite Keepers — Quillmark Institute</title>
<link rel="stylesheet" href="https://fonts.googleapis.com/css2?family=Inter:wght@600;700;800&display=swap">
<style>
  :root {
    --navy: #114769;
    --navy-dark: #0d3a57;
    --green: #76984C;
    --green-dark: #5d7f38;
    --seagull: #80B5CF;
    --seagull-dark: #6aa3c0;
    --plum: #8F2C63;
    --plum-dark: #792254;
    --ink: #191919;
    --paper: #ffffff;
  }
  * { box-sizing: border-box; margin: 0; padding: 0; }
  html, body { width: 1200px; height: 800px; overflow: hidden; background: var(--paper); }
  body { font-family: "Inter", Arial, sans-serif; position: relative; }

  .table {
    position: absolute; left: 210px; top: 30px;
    display: grid;
    grid-template-columns: repeat(6, 130px);
    grid-template-rows: repeat(4, 140px);
  }
  .element {
    position: relative;
    border: 6px solid var(--ink);
    margin: -3px;
    border-radius: 4px;
    color: var(--paper);
    overflow: hidden;
  }
  .element .name {
    position: absolute; top: 10px; right: 10px; left: 10px;
    font-size: 15px; font-weight: 700; line-height: 1.05; text-align: right;
  }
  .element .symbol {
    position: absolute; left: 10px; bottom: 6px;
    font-size: 54px; font-weight: 800; letter-spacing: -1px; line-height: 1;
  }
  .plum    { background: linear-gradient(135deg, var(--plum) 50%, var(--plum-dark) 50%); }
  .seagull { background: linear-gradient(135deg, var(--seagull) 50%, var(--seagull-dark) 50%); color: var(--ink); }
  .green   { background: linear-gradient(135deg, var(--green) 50%, var(--green-dark) 50%); }
  .navy    { background: linear-gradient(135deg, var(--navy) 50%, var(--navy-dark) 50%); }

  .gap { visibility: hidden; }

  .cat-mark {
    position: absolute; left: 12px; bottom: 12px;
    width: 62px; height: 56px; border-radius: 50%;
    background: var(--paper); border: 4px solid var(--ink);
  }

  .values {
    position: absolute; left: 210px; top: 625px;
    display: grid;
    grid-template-columns: repeat(5, 156px);
    grid-template-rows: 140px;
  }
  .values .name { text-align: center; }
  .heart { position: absolute; left: 14px; bottom: 18px; width: 52px; height: 48px; }
</style>
</head>
<body>
  <main class="table" aria-label="Amber Ledger of Kite Keepers">
    <div class="element plum"><span class="name">Anti-<br>violaci</span><span class="symbol">Av</span></div>
    <div class="gap"></div><div class="gap"></div><div class="gap"></div><div class="gap"></div>
    <div class="element green"><span class="name">Belonging</span><span class="symbol">B</span></div>

    <div class="element plum"><span class="name">Earth<br>Childha</span><span class="symbol">Ec</span></div>
    <div class="element seagull"><span class="name">Climate<br>Chanja</span><span class="symbol">Cc</span></div>
    <div class="element seagull"><span class="name">Environm<br>Justia</span><span class="symbol">Ej</span></div>
    <div class="element seagull"><span class="name">Human<br>Simta</span><span class="symbol">Hs</span></div>
    <div class="element seagull"><span class="name">Halth<br>Las</span><span class="symbol">Hl</span></div>
    <div class="element green"><span class="name">Honsing</span><span class="symbol">H</span></div>

    <div class="element plum"><span class="name">Education</span><span class="symbol">Ed</span></div>
    <div class="element seagull"><span class="name">Attn<br>Suncol</span><span class="symbol">As</span></div>
    <div class="element seagull"><span class="name">Social<br>Justia</span><span class="symbol">Sj</span></div>
    <div class="element seagull"><span class="name">Civil<br>Risht</span><span class="symbol">Cr</span></div>
    <div class="element seagull"><span class="name">Health<br>Equita</span><span class="symbol">He</span></div>
    <div class="element green"><span class="name">Jobs</span><span class="symbol">J</span></div>

    <div class="element plum"><span class="name">Animal<br>Weifare</span><span class="symbol">Aw</span></div>
    <div class="element seagull"><span class="name">Cat</span><div class="cat-mark" role="img" aria-label="Cat face icon"></div></div>
    <div class="element seagull"><span class="name">Racial<br>Justia</span><span class="symbol">Rj</span></div>
    <div class="element seagull"><span class="name">Inmijn<br>Risht</span><span class="symbol">Av</span></div>
    <div class="element seagull"><span class="name">Behavian<br>Halth</span><span class="symbol">Bh</span></div>
    <div class="element green"><span class="name">Inter-<br>generation</span><span class="symbol">Ig</span></div>
  </main>

  <section class="values" aria-label="Values">
    <div class="element navy"><span class="name">Love</span>
      <svg class="heart" viewBox="0 0 52 48" aria-label="Heart"><path d="M26 46 C10 32 2 24 2 14 C2 6 8 2 14 2 C20 2 24 6 26 10 C28 6 32 2 38 2 C44 2 50 6 50 14 C50 24 42 32 26 46Z" fill="#fff"/></svg>
    </div>
    <div class="element navy"><span class="name">Anthentia</span><span class="symbol">A</span></div>
    <div class="element navy"><span class="name">Hhmlita</span><span class="symbol">H</span></div>
    <div class="element navy"><span class="name">Andacith</span><span class="symbol">An</span></div>
    <div class="element navy"><span class="name">Justice</span><span class="symbol">J</span></div>
  </section>
</body>
</html>
```